Upscale business cards needed for Board of Directors

We need professional business cards created for members of our family business Board of Directors. We would like these relatively simple and straightforward, but also with a unique element to set them apart. Probably stick with neutral and simple colors - white, grey etc. We need space for the traditional elements, including name, title, address, email/phone number. And we will be creating several from this template so it needs to be template that is easy to switch information in and out of.
Business
See description

```html
<!DOCTYPE html>
<html lang="en">
<head>
<meta charset="utf-8">
<title>Northvale Holdings – Business Card</title>
<link rel="stylesheet" href="https://fonts.googleapis.com/css2?family=Roboto:wght@400;500;700&display=swap">
<style>
  :root {
    --stage: #2a2a2a;
    --card-dark: #1c1a1a;
    --card-light: #ffffff;
    --ink: #1e1e1e;
    --ink-soft: #5a5a5a;
    --gold: #b7a584;
    --rule: #3a3a3a;
    --paper-text: #f2f2f2;
  }
  * { box-sizing: border-box; margin: 0; padding: 0; }
  html, body {
    width: 1200px; height: 950px; overflow: hidden;
    background: var(--stage);
    font-family: "Roboto", Arial, sans-serif;
  }
  .canvas {
    width: 1200px; height: 950px;
    display: flex; flex-direction: column; align-items: center; justify-content: center;
    gap: 50px;
  }
  .card {
    width: 700px; height: 400px; position: relative;
    box-shadow: 0 12px 30px rgba(0,0,0,.45);
  }
  /* Front */
  .card--front { background: var(--card-dark); color: var(--paper-text); }
  .card--front .brand {
    position: absolute; left: 0; right: 0; top: 140px; text-align: center;
  }
  .brand__name {
    font-weight: 700; font-size: 44px; letter-spacing: 2px; line-height: 1; text-transform: uppercase;
  }
  .brand__sub {
    font-weight: 700; font-size: 22px; letter-spacing: 9px; line-height: 1; margin-top: 10px; text-transform: uppercase;
  }
  .card--front .website {
    position: absolute; left: 0; right: 0; top: 290px; text-align: center;
    font-size: 14px; letter-spacing: 4px; color: #d8d8d8;
  }
  /* Back */
  .card--back { background: var(--card-light); color: var(--ink); }
  .card--back .brand {
    position: absolute; right: 60px; top: 60px; text-align: center; color: var(--ink);
  }
  .card--back .brand .brand__name { font-size: 42px; }
  .card--back .brand .brand__sub { font-size: 21px; }
  .brand-rule {
    position: absolute; left: 330px; right: 40px; top: 180px; height: 1px; background: var(--rule);
  }
  .person { position: absolute; left: 45px; top: 268px; }
  .person__name { font-size: 22px; font-weight: 500; color: var(--ink); }
  .person__title { font-size: 16px; color: var(--gold); margin-top: 4px; }
  .contact-rule {
    position: absolute; left: 45px; right: 40px; top: 328px; height: 1px; background: #cfcfcf;
  }
  .contact { position: absolute; left: 45px; top: 338px; font-size: 14px; color: var(--ink-soft); line-height: 22px; }
  .contact b { color: var(--ink); font-weight: 700; }
  .contact span + span { margin-left: 12px; }
</style>
</head>
<body>
<main class="canvas">
  <section class="card card--front" aria-label="Card front">
    <div class="brand">
      <div class="brand__name">Northvale</div>
      <div class="brand__sub">Holdings</div>
    </div>
    <div class="website">www.northvale.com</div>
  </section>

  <section class="card card--back" aria-label="Card back">
    <div class="brand">
      <div class="brand__name">Northvale</div>
      <div class="brand__sub">Holdings</div>
    </div>
    <div class="brand-rule"></div>
    <div class="person">
      <div class="person__name">Marcus Hale</div>
      <div class="person__title">President</div>
    </div>
    <div class="contact-rule"></div>
    <div class="contact">
      <div>2719 Larkspur Avenue, Glen Harbor, NY 11020</div>
      <div>
        <span><b>P :</b> 555 0142 7781</span>
        <span><b>E :</b> marcus@northvale.com</span>
        <span><b>W :</b> www.northvale.com</span>
      </div>
    </div>
  </section>
</main>
</body>
</html>
```